Business Card for my New Brokerage

Looking to get a business card design for my new Real Estate Brokerage.
I want it with Picture, Phone Number, Email, Website, Office Address
Name and Designation. Please add logo too.

Target Market(s)

Real Estate Investors or Home Buyers

Industry/Entity Type

Real Estate

Contact Information for Business Card

Name, Email, Phone Number, website, email, office address

Colors
EB3D1F
EC4F4E
F09395
F8D3D4
FCEDEE

Requirements
Must have
• Minimalistic, Clean, Modern, Photo
Nice to have
• White and Red Colors

```html
<!DOCTYPE html>
<html lang="en">
<head>
<meta charset="utf-8">
<title>Ember Realty Inc – Business Card</title>
<link href="https://fonts.googleapis.com/css2?family=Montserrat:wght@400;500;600;700;800&display=swap" rel="stylesheet">
<style>
  :root {
    --brand-red: #e23a24;
    --ink: #2b2b2b;
    --paper: #ffffff;
    --stage: #e6e7e8;
    --skyline-light: #f1f2f3;
    --skyline-mid: #e3e4e6;
    --photo-top: #cfd3d9;
    --photo-bottom: #5f6b7a;
  }
  * { box-sizing: border-box; margin: 0; padding: 0; }
  html, body {
    width: 1187px;
    height: 1200px;
    overflow: hidden;
    background: var(--stage);
    font-family: "Montserrat", Arial, sans-serif;
  }
  .card {
    position: absolute;
    background: var(--paper);
    border-radius: 18px;
    overflow: hidden;
  }
  .card--front { left: 218px; top: 122px; width: 752px; height: 430px; }
  .card--back  { left: 214px; top: 644px; width: 760px; height: 434px; }

  .brand {
    position: absolute;
    color: var(--brand-red);
    font-weight: 700;
    text-align: center;
    line-height: 1;
  }
  .brand__name { display: block; letter-spacing: 1px; }
  .brand__sub { display: block; letter-spacing: 0.22em; }

  .card--front .brand { left: 0; width: 100%; top: 182px; }
  .card--front .brand__name { font-size: 76px; }
  .card--front .brand__sub { font-size: 22px; margin-top: 12px; }

  .skyline {
    position: absolute;
    left: 0; bottom: 0;
    width: 100%; height: 180px;
    background: linear-gradient(180deg, var(--skyline-light) 0%, var(--skyline-mid) 100%);
  }

  .portrait {
    position: absolute;
    left: 0; top: 29px;
    width: 377px; height: 405px;
    background: linear-gradient(180deg, var(--photo-top) 0%, var(--photo-bottom) 100%);
    z-index: 2;
  }
  .name-band {
    position: absolute;
    left: 0; top: 165px;
    width: 100%; height: 80px;
    background: var(--brand-red);
  }
  .card--back .brand { left: 443px; width: 245px; top: 52px; }
  .card--back .brand__name { font-size: 58px; }
  .card--back .brand__sub { font-size: 17px; margin-top: 8px; }

  .agent { position: absolute; left: 443px; top: 180px; color: var(--paper); }
  .agent__name { font-size: 29px; font-weight: 800; letter-spacing: 0.5px; line-height: 1; }
  .agent__title { font-size: 17px; font-weight: 500; margin-top: 10px; letter-spacing: 0.3px; }

  .address {
    position: absolute; left: 445px; top: 256px;
    font-size: 17px; font-weight: 500; color: var(--ink);
    line-height: 28px; letter-spacing: 0.3px;
  }
  .address::after {
    content: ""; display: block;
    width: 58px; height: 3px; margin-top: 6px;
    background: var(--brand-red);
  }
  .contacts {
    position: absolute; left: 445px; top: 333px;
    list-style: none;
    font-size: 17px; font-weight: 500; color: var(--ink);
    letter-spacing: 0.3px;
  }
  .contacts li { display: flex; align-items: center; height: 29px; }
  .contacts svg { width: 15px; height: 15px; margin-right: 8px; fill: var(--brand-red); flex: none; }
</style>
</head>
<body>

<section class="card card--front">
  <div class="skyline" role="img" aria-label="Faint grey city skyline illustration"></div>
  <div class="brand">
    <span class="brand__name">EMBER</span>
    <span class="brand__sub">REALTY INC</span>
  </div>
</section>

<section class="card card--back">
  <div class="name-band"></div>
  <div class="portrait" role="img" aria-label="Portrait photo of the agent in a grey suit and blue tie"></div>

  <div class="brand">
    <span class="brand__name">EMBER</span>
    <span class="brand__sub">REALTY INC</span>
  </div>

  <div class="agent">
    <div class="agent__name">MARCUS HALE</div>
    <div class="agent__title">Broker Associate</div>
  </div>

  <address class="address" style="font-style:normal">
    204 Harbor View Complex<br>
    Bayfront Science Park
  </address>

  <ul class="contacts">
    <li>
      <svg viewBox="0 0 24 24"><path d="M6.6 10.8a15.1 15.1 0 0 0 6.6 6.6l2.2-2.2c.3-.3.7-.4 1-.2 1.1.4 2.3.6 3.6.6.6 0 1 .4 1 1V20c0 .6-.4 1-1 1A17 17 0 0 1 3 4c0-.6.4-1 1-1h3.5c.6 0 1 .4 1 1 0 1.3.2 2.5.6 3.6.1.3 0 .7-.2 1z"/></svg>
      555-014-2290
    </li>
    <li>
      <svg viewBox="0 0 24 24"><path d="M2 5h20v14H2z M3.5 6.5v.6l8.5 6 8.5-6v-.6z" fill-rule="evenodd"/></svg>
      info@emberrealtyinc.com
    </li>
    <li>
      <svg viewBox="0 0 24 24"><path d="M12 2a10 10 0 1 0 0 20 10 10 0 0 0 0-20zm6.9 6h-2.8a15.6 15.6 0 0 0-1.4-3.6A8 8 0 0 1 18.9 8zM12 4c.8 1.2 1.5 2.5 1.9 4h-3.8c.4-1.5 1.1-2.8 1.9-4zM4.3 14a8.2 8.2 0 0 1 0-4h3.3a16.5 16.5 0 0 0 0 4zm.8 2h2.8c.3 1.3.8 2.5 1.4 3.6A8 8 0 0 1 5.1 16zm2.8-8H5.1a8 8 0 0 1 4.2-3.6C8.7 5.5 8.2 6.7 7.9 8zM12 20c-.8-1.2-1.5-2.5-1.9-4h3.8c-.4 1.5-1.1 2.8-1.9 4zm2.3-6H9.7a14.7 14.7 0 0 1 0-4h4.6a14.7 14.7 0 0 1 0 4zm.4 5.6c.6-1.1 1.1-2.3 1.4-3.6h2.8a8 8 0 0 1-4.2 3.6zm1.7-5.6a16.5 16.5 0 0 0 0-4h3.3a8.2 8.2 0 0 1 0 4z"/></svg>
      www.emberrealtyinc.com
    </li>
  </ul>
</section>

</body>
</html>
```